New Modern Wix Website Design

We are NOT your typical electrical/home improvement contractor, so we need our website updated. We already have a logo for each division.
We provided a neutral logo with a hard hat, a logo for the home improvement, and a logo for the electrical division. (if we can implement all 3 logos will be great but at least the 2 for the divisions must be used.

We looking for a website that a 10-year-old can understand, our target audience is the new young generation that wants innovations in their properties, smart homes, cool smart things/gadgets. So we need a website that is fun, simple, eye-catching. (we don't want to appear TOO serious and boring)
NO GENERIC WEBSITES SO MUST BE VERY CREATIVE!!!

We want to be able to share Reviews, a contact box, business hours, our services, etc...

current website kelvantrio.example

Target Market(s)

Contractors in different trades.

Industry/Entity Type

Construction

Colors
FFC000
F8CF3A
FAE287
FDF2CF
FEFAEE

Requirements
Must have
• Modern upmarket look and feel
Nice to have
• already attached supporting images.
Should not have
• basic typical construction boring and depressing look and feel.

```html
<!DOCTYPE html>
<html lang="en">
<head>
<meta charset="utf-8">
<title>Mr. Vantrio — Home Improvement &amp; Electrical Services</title>
<link href="https://fonts.googleapis.com/css2?family=Roboto:wght@400;500;700;900&display=swap" rel="stylesheet">
<style>
:root{
  --yellow:#FFC000;
  --yellow-soft:#F8CF3A;
  --butter:#FAE287;
  --cream:#FDF2CF;
  --ivory:#FEFAEE;
  --amber:#E9A800;
  --ink:#1a1a1a;
  --text:#3a3a3a;
  --white:#ffffff;
  --night:#141414;
}
*{box-sizing:border-box;margin:0;padding:0}
html,body{width:1200px;height:2679px;overflow:hidden}
body{font-family:'Roboto',sans-serif;color:var(--text);background:var(--ivory);position:relative}
.abs{position:absolute}
.btn{position:absolute;background:var(--yellow);color:var(--ink);font-weight:700;letter-spacing:3px;font-size:14px;display:flex;align-items:center;justify-content:center;border-radius:3px;box-shadow:0 5px 0 var(--amber)}

/* header */
.site-header{top:0;left:0;width:1200px;height:63px;background:var(--white);z-index:3;border-bottom:3px solid var(--yellow)}
.brand-badge{top:0;left:86px;width:194px;height:117px;background:var(--white);border-radius:0 0 60px 60px;z-index:4;display:flex;align-items:flex-end;justify-content:center;padding-bottom:22px;gap:8px;box-shadow:0 4px 0 var(--yellow)}
.brand-badge .dot{width:16px;height:16px;border-radius:50%;background:var(--yellow)}
.brand-badge .name{font-weight:900;font-size:21px;color:var(--ink)}
.main-nav{top:0;left:475px;height:63px;display:flex;gap:24px;align-items:center;font-size:14px;font-weight:500;color:var(--ink)}
.login{top:14px;left:993px;width:96px;height:36px;letter-spacing:4px;box-shadow:none}

/* hero */
.hero{top:63px;left:0;width:1200px;height:634px;background:linear-gradient(160deg,#262320 0%,#2f2a22 55%,#4a3a1c 100%)}
.hero-title{top:276px;left:0;width:1200px;text-align:center;font-size:72px;font-weight:700;color:var(--yellow);line-height:84px}
.hero-text{top:364px;left:225px;width:750px;text-align:center;color:var(--white);font-size:15.5px;line-height:23px;font-weight:500}
.hero-cta{top:452px;left:526px;width:148px;height:35px}
.arrow{top:372px}

/* division cards */
.division{width:480px;height:224px;top:623px;background:var(--yellow);padding:12px 10px;border-radius:6px;box-shadow:0 8px 20px rgba(233,168,0,.35);z-index:2}
.division .photo{width:100%;height:100%;border-radius:3px;background:linear-gradient(135deg,#2c2a28,#4d3c1c 60%,#1e1d1c);display:flex;flex-direction:column;align-items:center;justify-content:center;gap:14px}
.division .mark{font-weight:900;font-size:26px;color:var(--white);display:flex;align-items:center;gap:8px}
.division .mark i{width:14px;height:14px;border-radius:50%;background:var(--white);display:block}
.division .label{font-weight:700;font-size:22px;color:var(--yellow)}

/* welcome */
.welcome{top:697px;left:0;width:1200px;height:652px;background:linear-gradient(180deg,var(--ivory),var(--cream))}
.kicker{top:940px;left:0;width:1200px;text-align:center;font-size:21px;letter-spacing:6px;color:var(--ink);font-weight:500}
.welcome-title{top:978px;width:1200px;left:0;text-align:center;font-size:72px;font-weight:700;color:var(--yellow);line-height:80px}
.welcome-text{top:1073px;left:228px;width:744px;text-align:center;font-size:15.5px;line-height:23.5px;color:#444}
.welcome-text p+p{margin-top:23px}
.learn{top:1241px;left:475px;width:250px;height:36px}

/* reviews */
.reviews{top:1349px;left:0;width:1200px;height:517px;background:var(--butter)}
.rev-brand{top:1498px;left:111px;font-size:34px;font-weight:500;color:var(--ink)}
.rev-brand small{display:block;font-size:13px;color:var(--ink);letter-spacing:2px}
.rev-heading{top:1575px;left:111px;width:250px;font-size:27px;font-weight:700;line-height:36px;color:var(--ink)}
.view-more{top:1742px;left:111px;width:138px;height:36px;background:var(--ink);color:var(--yellow);box-shadow:0 5px 0 #000}
.review{top:1463px;width:337px;height:317px;padding:38px 16px 0;text-align:center;border-radius:6px;box-shadow:0 6px 16px rgba(160,110,0,.18)}
.review .stars{color:var(--amber);font-size:20px;letter-spacing:4px}
.review .quote{margin-top:16px;font-size:12.5px;line-height:20px;color:#444}
.review hr{width:44px;border:0;border-top:2px solid var(--yellow);margin:18px auto 24px}
.review .who{font-size:16.5px;font-weight:500;color:var(--ink)}
.review .role{font-size:11px;margin-top:5px;color:var(--ink)}

/* map & contact */
.map{top:1866px;left:0;width:1200px;height:584px;background:linear-gradient(120deg,#cfe3b4,#e6efc6 50%,#d3e6b6)}
.map-label{top:2218px;left:245px;font-size:15px;letter-spacing:3px;font-weight:700;color:var(--ink)}
.contact-card{top:1955px;left:608px;width:480px;height:401px;background:var(--yellow);padding:10px;border-radius:6px}
.contact-inner{width:100%;height:100%;background:var(--night);border-radius:3px;position:relative;color:var(--yellow-soft);font-size:14px}
.contact-inner h2{position:absolute;top:44px;left:35px;font-size:26px;font-weight:500;color:var(--yellow)}
.contact-inner h3{position:absolute;font-size:17px;font-weight:500;color:var(--yellow)}
.contact-inner .line{position:absolute;left:35px;display:flex;align-items:center;gap:6px}
.hours{position:absolute;left:277px;line-height:23px}
.socials{position:absolute;top:216px;left:35px;display:flex;gap:7px}
.socials span{width:16px;height:16px;border-radius:50%;background:var(--yellow)}
.email-field{position:absolute;top:310px;left:19px;width:238px;height:41px;border:1px solid var(--butter);border-radius:3px;color:var(--white);font-size:13px;display:flex;align-items:center;padding-left:18px}
.submit{top:310px;left:270px;width:170px;height:41px;box-shadow:none;letter-spacing:4px;font-size:15px}

/* footer */
.site-footer{top:2450px;left:0;width:1200px;height:229px;background:var(--night);color:var(--cream);font-size:12px;border-top:6px solid var(--yellow)}
.foot-nav{position:absolute;top:103px;left:112px;display:flex;gap:21px}
.foot-brand{position:absolute;top:89px;left:0;width:1200px;text-align:center;font-weight:900;font-size:24px;color:var(--yellow)}
.copy{position:absolute;top:103px;left:885px}
.code{position:absolute;top:103px;left:1136px}
</style>
</head>
<body>

<header class="abs site-header">
  <nav class="abs main-nav">
    <span>HOME</span><span>ABOUT</span><span>JOB OPPORTUNITIES</span><span>CONTACT</span><span>ABOUT</span><span>MORE</span>
  </nav>
  <div class="btn login">LOG IN</div>
</header>
<div class="abs brand-badge"><span class="dot"></span><span class="name">MR. VANTRIO</span></div>

<section class="abs hero" role="img" aria-label="Dark modern living and dining room interior"></section>
<h1 class="abs hero-title">MR. VANTRIO</h1>
<p class="abs hero-text">The contractors at Mr. Vantrio understand the importance of adhering to the highest quality standards in every project we take on. Since our founding in 2016, our expertise and careful craftsmanship have allowed us to provide long-lasting solutions for dozens of clients. Browse the site now to learn more.</p>
<div class="btn hero-cta">GET STARTED</div>
<svg class="abs arrow" style="left:33px" width="22" height="14" viewBox="0 0 22 14"><path d="M22 7H4M9 1L2 7l7 6" stroke="#FFC000" stroke-width="3" fill="none"/></svg>
<svg class="abs arrow" style="left:1144px" width="22" height="14" viewBox="0 0 22 14"><path d="M0 7h18M13 1l7 6-7 6" stroke="#FAE287" stroke-width="3" fill="none"/></svg>

<section class="abs welcome" role="img" aria-label="Faint architectural blueprint background"></section>

<div class="abs division" style="left:111px">
  <div class="photo" role="img" aria-label="Home improvement workers on site">
    <div class="mark"><i></i>MR. VANTRIO</div>
    <div class="label">HOME IMPROVEMENT</div>
  </div>
</div>
<div class="abs division" style="left:608px">
  <div class="photo" role="img" aria-label="Electrician testing a wiring panel">
    <div class="mark"><i></i>MR. VANTRIO</div>
    <div class="label">ELECTRICAL SERVICES</div>
  </div>
</div>

<p class="abs kicker">WELCOME TO</p>
<h2 class="abs welcome-title">MR. VANTRIO</h2>
<div class="abs welcome-text">
  <p>We founded Mr. Vantrio out of a pure passion for people. Our goals, our ambitions, our inspirations, all come together to form a truly amazing company that all of us are proud to be a part of.</p>
  <p>Since opening back in 2016, we have become masters at our craft. We go above and beyond your requests to keep you coming back for more. Explore the rest of our site to learn more about what we offer, and get in touch with any questions.</p>
</div>
<div class="btn learn">LEARN MORE ABOUT US</div>

<section class="abs reviews"></section>
<svg class="abs" style="top:1434px;left:1013px" width="22" height="14" viewBox="0 0 22 14"><path d="M22 7H4M9 1L2 7l7 6" stroke="#1a1a1a" stroke-width="3" fill="none"/></svg>
<svg class="abs" style="top:1434px;left:1050px" width="22" height="14" viewBox="0 0 22 14"><path d="M0 7h18M13 1l7 6-7 6" stroke="#E9A800" stroke-width="3" fill="none"/></svg>
<div class="abs rev-brand">Reviews<small>★★★★★</small></div>
<h3 class="abs rev-heading">Neque porro quisquam est qui dolorem ipsum quia dolor sit amet,</h3>
<div class="btn view-more">VIEW MORE</div>

<article class="abs review" style="left:398px;background:var(--ivory)">
  <div class="stars">★★★★☆</div>
  <p class="quote">Lorem Ipsum is simply dummy text of the printing and typesetting industry. Lorem Ipsum has been the industry's standard dummy text ever since the 1500s, when an unknown printer took a galley of type and scrambled it to make a type specimen book. It has survived not only five centuries,</p>
  <hr><p class="who">Daniel R Moreau</p><p class="role">Office and Administrative</p>
</article>
<article class="abs review" style="left:752px;background:var(--white)">
  <div class="stars">★★★★☆</div>
  <p class="quote">Lorem Ipsum is simply dummy text of the printing and typesetting industry. Lorem Ipsum has been the industry's standard dummy text ever since the 1500s, when an unknown printer took a galley of type and scrambled it to make a type specimen book. It has survived not only five centuries,</p>
  <hr><p class="who">Daniel R Moreau</p><p class="role">Office and Administrative</p>
</article>

<section class="abs map" role="img" aria-label="Regional road map around the service area"></section>
<svg class="abs" style="top:2082px;left:283px" width="82" height="108" viewBox="0 0 82 108"><path d="M41 0C18 0 0 18 0 41c0 29 41 67 41 67s41-38 41-67C82 18 64 0 41 0z" fill="#FFC000"/><circle cx="41" cy="40" r="16" fill="#FEFAEE"/></svg>
<div class="abs map-label">MR. VANTRIO</div>

<section class="abs contact-card">
  <div class="contact-inner">
    <h2>CONTACT</h2>
    <h3 style="top:54px;left:270px">BUSINESS HOURS</h3>
    <div class="line" style="top:100px">
      <svg width="16" height="12" viewBox="0 0 16 12"><path d="M0 1l5-1 6 1 5-1v11l-5 1-6-1-5 1z" fill="#FFC000"/></svg>- Fairview, PA 17000</div>
    <div class="line" style="top:138px">
      <svg width="14" height="11" viewBox="0 0 14 11"><rect width="14" height="11" fill="#FFC000"/><path d="M0 0l7 6 7-6" stroke="#141414" fill="none"/></svg>- info@kelvantrio.example</div>
    <div class="line" style="top:176px">
      <svg width="13" height="13" viewBox="0 0 13 13"><path d="M3 0l2 3-1.5 2c1 2 2.5 3.5 4.5 4.5L10 8l3 2-1 3C6 13 0 7 0 1z" fill="#FFC000"/></svg>- +1 (555) 014-2767</div>
    <div class="socials"><span></span><span></span><span></span><span></span></div>
    <div class="hours" style="top:99px">Wednesday to Friday<br>6am–6pm</div>
    <div class="hours" style="top:162px">Saturday To Sunday<br>Closed</div>
    <h3 style="top:262px;left:184px">SUBSCRIBE</h3>
    <div class="email-field">Email Address</div>
    <div class="btn submit">SUBMIT NOW</div>
  </div>
</section>

<footer class="abs site-footer">
  <nav class="foot-nav"><span>HOME</span><span>ABOUT</span><span>JOB OPPORTUNITIES</span><span>CONTACT</span><span>ABOUT</span></nav>
  <div class="foot-brand">MR. VANTRIO</div>
  <span class="copy">COPYRIGHT © 2021 MR. VANTRIO.</span>
  <span class="code">C24</span>
</footer>

</body>
</html>
```